Letterhead for a German Distribution/Manufacturing Company

We need a professional Letterhead in a unique Design.
not to playful.
The Letterhead has to show show that we are a international company with headquater in Germany.
all details like adress, Vat Tax Number, Bank Accout, Eori, email, Company number has to be on the Letterhead.
for example use: VAT TAX DE5470318 Bank Account: Kestrel Bank IBAN DE412058731ß204683 Swift: MORV0417352 EORI 3150428697 Company Number: HRB 51806 Adress: VOLMINTA UG Ahornweg 7 Postal Code 06384 City Burgstädt Country: Germany Email: info@volminta-example.com
the design can be colored but doesnt have to be
Industry/Entity Type
Manufacturing and international distribution
Requirements
Must have
- show that we are a international company with headquater in Germany. our company infos and logo

```html
<!DOCTYPE html>
<html lang="en">
<head>
<meta charset="utf-8">
<title>Volminta Letterhead</title>
<link href="https://fonts.googleapis.com/css2?family=Poppins:wght@400;500;600;700&family=Great+Vibes&display=swap" rel="stylesheet">
<style>
  :root{
    --bg:#dcdcdc;
    --paper:#ffffff;
    --ink:#1c1c1c;
    --band:#1e1e1e;
    --purple:#5b2b72;
    --rust:#a3503a;
    --maroon:#6e2a4e;
  }
  *{margin:0;padding:0;box-sizing:border-box}
  html,body{width:672px;height:1200px;overflow:hidden;background:var(--bg)}
  body{position:relative;font-family:'Poppins',sans-serif;color:var(--ink)}
  .sheet-frame{position:absolute;left:16px;top:186px;width:640px;height:827px;box-shadow:0 4px 14px rgba(0,0,0,.18)}
  .sheet{position:absolute;left:0;top:0;width:940px;height:1215px;background:var(--paper);transform:scale(.6809);transform-origin:0 0;overflow:hidden}
  .sheet-shapes{position:absolute;left:0;top:0}
  .abs{position:absolute}
  .brand{left:95px;top:92px;display:flex;align-items:center;gap:16px}
  .brand-dot{width:58px;height:58px;border-radius:50%;background:var(--ink)}
  .brand-name{font-size:46px;font-weight:500;letter-spacing:1px;color:var(--ink)}
  .tagline{left:594px;top:58px;color:#fff;font-weight:600;font-size:18px;line-height:1.2}
  .hq{left:674px;top:92px;display:flex;align-items:center;gap:8px;color:#fff;font-weight:600;font-size:14px;line-height:1.25}
  .flag{width:34px;height:21px;display:flex;flex-direction:column}
  .flag i{flex:1}
  .sender-name{left:94px;top:242px;font-size:20px;font-weight:700;color:var(--maroon)}
  .sender-role{left:94px;top:268px;font-size:15px;font-weight:600}
  .contact{left:94px;top:302px;font-size:13.5px;font-weight:500;line-height:17px}
  .contact div{display:flex;margin-bottom:7px}
  .contact b{width:26px;color:var(--maroon);font-weight:700}
  .date{left:578px;top:367px;font-size:13.5px;font-weight:500}
  .date b,.footer b{font-weight:700}
  .date b{color:var(--maroon)}
  .body-text{left:97px;top:435px;width:760px;font-size:13.5px;line-height:16.7px}
  .body-text p{margin-bottom:28px}
  .signature{left:92px;top:782px;font-family:'Great Vibes',cursive;font-size:36px}
  .footer{font-size:12px;line-height:15px}
  .footer .row{display:flex;align-items:flex-start;gap:6px;margin-bottom:10px}
  .footer .row.plain{padding-left:20px}
  .icon{width:15px;height:15px;flex:none;margin-top:0}
  .footer-left{left:95px;top:1030px;width:330px}
  .footer-right{left:448px;top:1030px;width:470px}
</style>
</head>
<body>
<div class="sheet-frame">
  <div class="sheet">
    <svg class="sheet-shapes" width="940" height="1215" viewBox="0 0 940 1215">
      <defs>
        <linearGradient id="stripe" x1="0" x2="1"><stop offset="0" stop-color="#5b2b72"/><stop offset="1" stop-color="#a3503a"/></linearGradient>
        <linearGradient id="stripe-rev" x1="0" x2="1"><stop offset="0" stop-color="#a3503a"/><stop offset="1" stop-color="#5b2b72"/></linearGradient>
      </defs>
      <polygon points="0,0 487,0 500,14 0,14" fill="#1e1e1e"/>
      <polygon points="0,23 506,23 518,39 0,39" fill="url(#stripe)"/>
      <polygon points="501,0 940,0 940,157 615,157" fill="#1e1e1e"/>
      <polygon points="0,1153 480,1153 542,1215 0,1215" fill="#1e1e1e"/>
      <polygon points="514,1181 940,1181 940,1195 528,1195" fill="url(#stripe-rev)"/>
      <polygon points="534,1201 940,1201 940,1215 548,1215" fill="#1e1e1e"/>
    </svg>

    <div class="abs brand"><span class="brand-dot"></span><span class="brand-name">VOLMINTA</span></div>

    <div class="abs tagline">INTERNATIONAL COMPANY</div>
    <div class="abs hq">
      <span class="flag" role="img" aria-label="Flag of Germany"><i style="background:#000"></i><i style="background:#dd0000"></i><i style="background:#ffce00"></i></span>
      <span>HEADQUARTER IN<br>GERMANY</span>
    </div>

    <div class="abs sender-name">HENRIK VALE</div>
    <div class="abs sender-role">chief director</div>
    <div class="abs contact">
      <div><b>A:</b><span>Suite 14, Marlow Court 58 Fenwick Rd,<br>Leeds, West Yorkshire LS7 2QD, GB</span></div>
      <div><b>W:</b><span>www.volminta-example.com</span></div>
      <div><b>P:</b><span>604318275</span></div>
    </div>
    <div class="abs date"><b>DATE:</b> 03.04.2023</div>

    <div class="abs body-text">
      <p>Lorem Ipsum is simply dummy text of the printing and typesetting industry. Lorem Ipsum has been the industry's standard dummy text ever since the 1500s, when an unknown printer took a galley of type and scrambled it to make a type specimen book. It has survived not only five centuries, but also the leap into electronic typesetting, remaining essentially unchanged.</p>
      <p>It is a long established fact that a reader will be distracted by the readable content of a page when looking at its layout. The point of using Lorem Ipsum is that it has a more-or-less normal distribution of letters, as opposed to using 'Content here, content here', making it look like readable English. Many desktop publishing packages and web page editors now use Lorem Ipsum as their default model text, and a search for 'lorem ipsum' will uncover many web sites still in their infancy. Various versions have evolved over the years, sometimes by accident, sometimes on purpose (injected humour and the like).</p>
      <p>There are many variations of passages of Lorem Ipsum available, but the majority have suffered alteration in some form, by injected humour, or randomised words which don't look even slightly believable. If you are going to use a passage of Lorem Ipsum, you need to be sure there isn't anything embarrassing hidden in the middle of text.</p>
    </div>

    <div class="abs signature">Henrik Vale</div>

    <div class="abs footer footer-left">
      <div class="row"><svg class="icon" viewBox="0 0 16 16"><rect x="1" y="1" width="14" height="14" rx="2" fill="#5b2b72"/><rect x="4" y="7" width="3" height="6" fill="#fff"/><rect x="9" y="4" width="3" height="9" fill="#fff"/></svg><span><b>COMPANY NUMBER:</b> HRB 51806</span></div>
      <div class="row"><svg class="icon" viewBox="0 0 16 16"><path d="M8 1a5 5 0 0 0-5 5c0 4 5 9 5 9s5-5 5-9a5 5 0 0 0-5-5z" fill="#5b2b72"/><circle cx="8" cy="6" r="2" fill="#fff"/></svg><span><b>ADDRESS:</b> VOLMINTA UG Ahornweg 7 Postal<br>&nbsp;&nbsp;&nbsp;&nbsp;&nbsp;&nbsp;&nbsp;&nbsp;&nbsp;&nbsp;&nbsp;&nbsp;&nbsp;&nbsp;&nbsp;&nbsp;&nbsp;&nbsp;Code 06384 City Burgstädt</span></div>
      <div class="row"><svg class="icon" viewBox="0 0 16 16"><rect x="2" y="1" width="1.6" height="14" fill="#5b2b72"/><path d="M3.6 2h10l-2.5 3.5 2.5 3.5h-10z" fill="#5b2b72"/></svg><span><b>COUNTRY:</b> Germany</span></div>
      <div class="row"><svg class="icon" viewBox="0 0 16 16"><rect x="1" y="3" width="14" height="10" fill="#5b2b72"/><path d="M1 3l7 6 7-6" stroke="#fff" stroke-width="1.3" fill="none"/></svg><span><b>EMAIL:</b> info@volminta-example.com</span></div>
    </div>

    <div class="abs footer footer-right">
      <div class="row"><svg class="icon" viewBox="0 0 16 16"><rect x="2" y="1" width="12" height="14" rx="1" fill="#5b2b72"/><path d="M5 5h6M5 8h6M5 11h4" stroke="#fff" stroke-width="1.3"/></svg><span><b>VAT TAX :</b> DE5470318</span></div>
      <div class="row"><svg class="icon" viewBox="0 0 16 16"><circle cx="8" cy="8" r="7" fill="#5b2b72"/><circle cx="8" cy="6" r="2.2" fill="#fff"/><path d="M4 12.5a4 4 0 0 1 8 0" fill="#fff"/></svg><span><b>BANK ACCOUNT:</b>&nbsp; KESTREL BANK IBAN DE412058731ß204683</span></div>
      <div class="row plain"><span><b>SWIFT:</b> MORV0417352</span></div>
      <div class="row plain"><span><b>EORI:</b> 3150428697</span></div>
    </div>
  </div>
</div>
</body>
</html>
```